BUSINESS CARD DESIGN

NAME- DALE VORSKIN
PHONE NUMER - 555- 714-9082
EMAIL- OFFICE@TRV-GROUNDMAKRZ.COM
BACK OF CARD- SPEACIALIZES IN LAND CLEARING, FORESTRY MUCLHING AND EXCAVATION

Contact Information for Business Card

NAME- DALE VORSKIN PHONE NUMER - 555- 714-9082 EMAIL- OFFICE@TRV-GROUNDMAKRZ.COM BACK OF CARD- SPEACIALIZES IN LAND CLEARING , MUCLHING AND EXCAVATION

```html
<!DOCTYPE html>
<html lang="en">
<head>
<meta charset="utf-8">
<title>Traverse Ground Makrz – Business Card</title>
<link href="https://fonts.googleapis.com/css2?family=Orbitron:wght@800&family=Poppins:wght@400;500&display=swap" rel="stylesheet">
<style>
  :root {
    --stage: #2a2a2c;
    --card: #1b1c1e;
    --gold: #f5b617;
    --rule: #6b6b6b;
    --pattern-light: #3d3e41;
    --pattern-dark: #141416;
  }
  * { box-sizing: border-box; margin: 0; padding: 0; }
  html, body { width: 1200px; height: 1108px; overflow: hidden; }
  body {
    background: var(--stage);
    position: relative;
    font-family: "Poppins", sans-serif;
    color: var(--gold);
  }
  .card {
    position: absolute;
    top: 170px;
    width: 500px;
    height: 770px;
    background: var(--card);
    border-radius: 26px;
    overflow: hidden;
  }
  .card--front { left: 70px; }
  .card--back { left: 630px; }

  /* front */
  .brand {
    position: absolute;
    top: 90px; left: 0; right: 0;
    text-align: center;
  }
  .brand__mark {
    width: 120px; height: 120px;
    border: 6px solid var(--gold);
    border-radius: 50%;
    margin: 0 auto 22px;
  }
  .brand__name {
    font-family: "Orbitron", sans-serif;
    font-weight: 800;
    font-size: 30px;
    letter-spacing: 1px;
    line-height: 1.2;
  }
  .brand__sub {
    font-family: "Orbitron", sans-serif;
    font-weight: 800;
    font-size: 18px;
    letter-spacing: 8px;
    line-height: 1.4;
  }
  .brand__line {
    width: 300px; height: 2px;
    background: var(--gold);
    margin: 8px auto;
  }
  .brand__phone {
    font-family: "Orbitron", sans-serif;
    font-weight: 800;
    font-size: 14px;
    letter-spacing: 9px;
    margin-top: 6px;
  }
  .person {
    position: absolute;
    top: 470px; left: 0; right: 0;
    text-align: center;
    font-family: "Orbitron", sans-serif;
    font-weight: 800;
    font-size: 34px;
    letter-spacing: 1px;
  }
  .contact-bar {
    position: absolute;
    top: 540px; left: 60px; right: 60px;
    display: flex; align-items: center; gap: 12px;
  }
  .contact-bar__rule { flex: 1; height: 1px; background: var(--rule); }
  .contact-bar__icon {
    width: 40px; height: 40px;
    background: var(--gold);
    border-radius: 6px;
    display: flex; align-items: center; justify-content: center;
  }
  .contact-list {
    position: absolute;
    top: 600px; left: 0; right: 0;
    text-align: center;
    font-size: 22px;
    line-height: 1.5;
  }

  /* back */
  .back__pattern {
    position: absolute; inset: 0;
    background: radial-gradient(circle at 85% 10%, var(--pattern-light), var(--card) 55%, var(--pattern-dark));
  }
  .back__brand {
    position: absolute;
    right: 40px; top: 560px;
    display: flex; align-items: center; gap: 10px;
    font-family: "Orbitron", sans-serif;
    font-weight: 800;
    font-size: 16px;
    text-align: right;
    line-height: 1.2;
  }
  .back__brand-mark {
    width: 34px; height: 34px;
    border: 4px solid var(--gold);
    border-radius: 50%;
  }
  .services {
    position: absolute;
    top: 650px; left: 0; right: 0;
    display: flex; justify-content: center; align-items: center; gap: 10px;
    font-size: 19px;
    letter-spacing: 0.5px;
  }
  .services__dot {
    width: 14px; height: 14px;
    background: var(--gold);
    border-radius: 50%;
  }
</style>
</head>
<body>
  <section class="card card--front">
    <div class="brand">
      <div class="brand__mark"></div>
      <div class="brand__name">TRAVERSE GROUND</div>
      <div class="brand__line"></div>
      <div class="brand__sub">MAKRZ LLC</div>
      <div class="brand__sub">HAWAII</div>
      <div class="brand__line"></div>
      <div class="brand__phone">555-714-9082</div>
    </div>

    <div class="person">DALE VORSKIN</div>

    <div class="contact-bar">
      <span class="contact-bar__rule"></span>
      <span class="contact-bar__icon">
        <svg width="24" height="24" viewBox="0 0 24 24" aria-hidden="true"><path d="M6 3l3 0 2 5-2 1.5a11 11 0 0 0 5.5 5.5L16 13l5 2v3a2 2 0 0 1-2 2A16 16 0 0 1 4 5a2 2 0 0 1 2-2z" fill="#1b1c1e"/></svg>
      </span>
      <span class="contact-bar__icon">
        <svg width="24" height="24" viewBox="0 0 24 24" aria-hidden="true"><rect x="3" y="6" width="18" height="12" fill="none" stroke="#1b1c1e" stroke-width="2"/><path d="M3 6l9 7 9-7" fill="none" stroke="#1b1c1e" stroke-width="2"/></svg>
      </span>
      <span class="contact-bar__icon">
        <svg width="24" height="24" viewBox="0 0 24 24" aria-hidden="true"><circle cx="12" cy="12" r="9" fill="none" stroke="#1b1c1e" stroke-width="2"/><path d="M3 12h18M12 3c3 3 3 15 0 18M12 3c-3 3-3 15 0 18" fill="none" stroke="#1b1c1e" stroke-width="1.5"/></svg>
      </span>
      <span class="contact-bar__rule"></span>
    </div>

    <div class="contact-list">
      <p>555- 714-9082</p>
      <p>office@trv-groundmakrz.com</p>
      <p>www.trv-groundmakrz.com</p>
    </div>
  </section>

  <section class="card card--back">
    <div class="back__pattern" role="img" aria-label="Repeating embossed company emblem pattern in glossy black"></div>
    <div class="back__brand">
      <span>TRAVERSE<br>GROUND MAKRZ</span>
      <span class="back__brand-mark"></span>
    </div>
    <div class="services">
      <span>LAND CLEARING</span>
      <span class="services__dot"></span>
      <span>MULCHING</span>
      <span class="services__dot"></span>
      <span>EXCAVATION</span>
    </div>
  </section>
</body>
</html>
```